Brellwick Partners, LLC Stationary

Brellwick Partners, LLC is a new financial planning and consulting company. We are looking for designs on business cards, letterhead, envelopes, and anything else that would be useful. Our preference for business card design is two sided. We are looking for a professional and clean look with incorporating the logo and patriotic feel. Thank you to all who participate and good luck!

```html
<!DOCTYPE html>
<html lang="en">
<head>
<meta charset="utf-8">
<title>Brellwick Partners, LLC – Business Card</title>
<link href="https://fonts.googleapis.com/css2?family=Arimo:wght@400;700&display=swap" rel="stylesheet">
<style>
  :root {
    --navy: #1d4373;
    --red: #c8202a;
    --red-deep: #a3151d;
    --ink: #4a4a4a;
    --paper: #ffffff;
    --paper-shade: #eef0f3;
    --backdrop: #d9dbde;
  }
  * { box-sizing: border-box; margin: 0; padding: 0; }
  html, body { width: 1200px; height: 950px; overflow: hidden; }
  body {
    background: var(--backdrop);
    font-family: "Arimo", sans-serif;
    display: flex;
    flex-direction: column;
    align-items: center;
    justify-content: center;
    gap: 50px;
  }
  .card {
    width: 630px;
    height: 360px;
    position: relative;
    overflow: hidden;
    box-shadow: 0 6px 18px rgba(0,0,0,.18);
  }

  /* Front */
  .card-front {
    background: linear-gradient(135deg, var(--paper) 55%, var(--paper-shade));
  }
  .side-band {
    position: absolute; left: 0; top: 0; bottom: 0;
    width: 78px;
    background: var(--navy);
  }
  .faint-mark {
    position: absolute;
    right: 40px; top: 90px;
    width: 240px; height: 240px;
    border-radius: 50%;
    background: var(--navy);
    opacity: .06;
  }
  .brand {
    position: absolute;
    left: 56px; top: 44px;
    display: flex; align-items: center; gap: 14px;
  }
  .brand-square {
    width: 44px; height: 44px;
    background: var(--red);
  }
  .brand-name {
    font-size: 30px;
    font-weight: 700;
    color: var(--navy);
    letter-spacing: .5px;
    line-height: 1;
  }
  .brand-tagline {
    position: absolute;
    left: 114px; top: 86px;
    font-size: 9px;
    letter-spacing: 1.6px;
    text-transform: uppercase;
    color: var(--navy);
  }
  .contact {
    position: absolute;
    left: 114px; top: 116px;
    color: var(--ink);
  }
  .person-name { font-size: 21px; font-weight: 700; color: var(--navy); }
  .person-title { font-size: 16px; color: var(--red); margin-bottom: 12px; }
  .address { font-size: 16px; line-height: 1.3; margin-bottom: 6px; }
  .contact-list { list-style: none; font-size: 16px; }
  .contact-list li { display: flex; align-items: center; gap: 9px; line-height: 1.4; }
  .contact-list svg { width: 15px; height: 15px; fill: var(--navy); flex: none; }

  /* Back */
  .card-back {
    background: linear-gradient(120deg, var(--red) 0%, var(--red-deep) 100%);
    display: flex; flex-direction: column;
    align-items: center; justify-content: center;
    gap: 22px;
  }
  .back-brand { display: flex; align-items: center; gap: 16px; }
  .back-brand .brand-square { background: var(--paper); width: 52px; height: 52px; }
  .back-brand .brand-name { color: var(--paper); font-size: 34px; }
  .back-web { color: var(--paper); font-size: 16px; letter-spacing: 2px; opacity: .85; }
</style>
</head>
<body>

<section class="card card-front">
  <div class="side-band"></div>
  <div class="faint-mark"></div>

  <div class="brand">
    <div class="brand-square"></div>
    <span class="brand-name">BRELLWICK PARTNERS, LLC</span>
  </div>
  <p class="brand-tagline">Financial Planning and Consulting</p>

  <div class="contact">
    <p class="person-name">Marcus Hale</p>
    <p class="person-title">President</p>
    <p class="address">2716 Larkspur Avenue<br>Ashford Glen, NY 11590</p>
    <ul class="contact-list">
      <li>
        <svg viewBox="0 0 24 24"><path d="M6.6 10.8a15 15 0 0 0 6.6 6.6l2.2-2.2c.3-.3.7-.4 1-.2 1.1.4 2.3.6 3.6.6.6 0 1 .4 1 1V20c0 .6-.4 1-1 1A17 17 0 0 1 3 4c0-.6.4-1 1-1h3.5c.6 0 1 .4 1 1 0 1.3.2 2.5.6 3.6.1.3 0 .7-.2 1z"/></svg>
        555 0142 7781
      </li>
      <li>
        <svg viewBox="0 0 24 24"><path d="M7 3h10v5H7zM4 9h16a2 2 0 0 1 2 2v7h-4v3H6v-3H2v-7a2 2 0 0 1 2-2zm4 8v2h8v-2z"/></svg>
        555 0168 3094
      </li>
      <li>
        <svg viewBox="0 0 24 24"><path d="M2 5h20v14H2zm2 2v.5l8 5 8-5V7z"/></svg>
        marcus@brellwick.com
      </li>
      <li>
        <svg viewBox="0 0 24 24"><path d="M12 2a10 10 0 1 0 0 20 10 10 0 0 0 0-20zm0 2c1 1.3 1.8 3 2.1 5H9.9C10.2 7 11 5.3 12 4zM4.3 11h3.6a16 16 0 0 0 0 2H4.3a8 8 0 0 1 0-2zm5.6 0h4.2a14 14 0 0 1 0 2H9.9a14 14 0 0 1 0-2zm6.2 0h3.6a8 8 0 0 1 0 2h-3.6a16 16 0 0 0 0-2zM9.9 15h4.2c-.3 2-1.1 3.7-2.1 5-1-1.3-1.8-3-2.1-5z"/></svg>
        www.brellwick.com
      </li>
    </ul>
  </div>
</section>

<section class="card card-back">
  <div class="back-brand">
    <div class="brand-square"></div>
    <span class="brand-name">BRELLWICK PARTNERS, LLC</span>
  </div>
  <p class="back-web">www.brellwick.com</p>
</section>

</body>
</html>
```